Lush Satchel

I am developing a web site which sells preowned high end designer handbags and accessories. Some of the brands include: Varenne, Marcel Ostrand & Belmo, to name a few. I am after a luxurious and high end feel.

Some brands I like that express this feel include: Quintel, Belmo, fabcloset.com, pursepassonpaw.com

I am after a logo, business card, letterhead, with compliments, address label and envelope designs.
The business name is Lush satchel, and the website will be www.lushsatchel.com.au. I have thoughts of using LSC as a logo or LUSH satchel.com.au

I don't want a large logo, it needs to blend in with the name in some way - or may not need an image at all, if the style of the font speaks to the brand.

Thank-you
Updates

Project Deadline Extended
Reason: I would like to give designers plenty of time to be able to submit a design.

Target Market(s)

Women, aged 25-60 who are into fashion

Industry/Entity Type

Business

Requirements
Must have
• High End
Luxurious

```html
<!DOCTYPE html>
<html lang="en">
<head>
<meta charset="utf-8">
<title>Lush Satchel – Business Cards</title>
<link rel="stylesheet" href="https://fonts.googleapis.com/css2?family=Source+Sans+3:wght@400;600;700&display=swap">
<style>
  :root {
    --crimson: #c0223f;
    --ink: #1e1a1b;
    --paper: #ffffff;
  }
  html, body {
    margin: 0;
    padding: 0;
    width: 1031px;
    height: 1200px;
    overflow: hidden;
    background: var(--paper);
  }
  .sheet {
    display: block;
    width: 1031px;
    height: 1200px;
    font-family: "Source Sans 3", "Myriad Pro", Arial, sans-serif;
  }
  .card-edge { fill: var(--paper); stroke: var(--ink); stroke-width: 3; }
  .brand-panel { fill: var(--crimson); }
  .panel-edge { fill: none; stroke: var(--ink); stroke-width: 3; stroke-linejoin: round; }
  .brand-mark { fill: var(--crimson); }
  .brand-name { fill: var(--crimson); font-size: 30px; font-weight: 600; }
  .site-url { fill: var(--ink); font-size: 23px; font-weight: 700; }
  .contact { fill: var(--paper); font-size: 34px; font-weight: 400; }
  .contact-accent { fill: var(--crimson); }
</style>
</head>
<body>
<svg class="sheet" viewBox="0 0 1031 1200" xmlns="http://www.w3.org/2000/svg" role="img" aria-label="Two Lush Satchel business card layouts">

  <!-- Card one: contact details stacked, email below -->
  <g class="card card-one">
    <rect class="card-edge" x="27" y="8" width="970" height="566" rx="85"/>
    <path class="brand-panel" d="M468 4 C 425 200, 440 420, 620 560 C 650 580, 700 578, 760 578 L 992 578 C 1004 540, 1006 430, 1002 320 C 1006 210, 1010 100, 996 18 C 985 8, 960 10, 940 6 Z"/>
    <path class="panel-edge" d="M940 6 C 965 10, 985 8, 996 18 C 1010 100, 1006 210, 1002 320 C 1006 430, 1004 540, 992 578"/>

    <rect class="brand-mark" x="100" y="70" width="150" height="150"/>
    <text class="brand-name" x="76" y="290">Lush Satchel</text>
    <text class="site-url" x="76" y="348">lushsatchel.com.au</text>

    <text class="contact" x="549" y="408">Elise Marlow</text>
    <text class="contact" x="583" y="458">Director</text>
    <text class="contact" x="604" y="505">0412 867 209</text>
    <text class="contact contact-accent" x="596" y="549" text-anchor="end">elisemarlow</text>
    <text class="contact" x="622" y="549">@lushsatchel</text>
  </g>

  <!-- Card two: email on top, contact details at the foot -->
  <g class="card card-two">
    <rect class="card-edge" x="4" y="622" width="1000" height="574" rx="85"/>
    <path class="brand-panel" d="M448 618 C 412 820, 440 1060, 648 1196 L 1000 1196 C 1012 1150, 1016 1040, 1012 930 C 1016 820, 1018 720, 1004 650 C 990 630, 960 626, 930 618 Z"/>
    <path class="panel-edge" d="M930 618 C 960 626, 990 630, 1004 650 C 1018 720, 1016 820, 1012 930 C 1016 1040, 1012 1150, 1000 1196"/>

    <rect class="brand-mark" x="90" y="686" width="150" height="150"/>
    <text class="brand-name" x="57" y="906">Lush Satchel</text>
    <text class="site-url" x="57" y="971">lushsatchel.com.au</text>

    <text class="contact" x="441" y="739">elisemarlow @lushsatchel</text>
    <text class="contact" x="559" y="1043">Elise Marlow</text>
    <text class="contact" x="595" y="1093">Director</text>
    <text class="contact" x="616" y="1140">0412 867 209</text>
  </g>
</svg>
</body>
</html>
```